Design Sales-Funnel page for our beauty brand*

Hi all,

we are a beauty brand located in Romania (Eastern-Europe) and we are using sales-funnel pages to sell our own make-up brushes.

We have a ready design (see download-link) that we are not totally happy with, so we want you to create a new version of it, which fits more to our companies website

www.lumavela.rowhich

is very clean and easy to read for our customers.

So, your task is to

1) re-create the main page of our sales funnel
2) according to your design from 1) create the upsell/downsell and thank-you page as well.

What we do not like about the actual design:
- it is not clean/simple enough = hard for the customer eye to catch the content. What do we mean with that? There are too many background frames, too many different colors used.
- The original price for our brushes is 1.299 LEI and for this sale, we are giving it away for 399 LEI (LEI = Romanian currency). The discount is 70%, but it does not show on the page enough.

You can download all files here:
https://www.filecrate-share.com/sh/4kqtpx2mw915bd/QXZrTnHvLpEeKcYwMbDoUfsJa?dl=0

Thanks,
Mirela

Target Market(s)

Women 18-35

Industry/Entity Type

Makeup

Number of Pages Required

4 page

Font styles to use
Sans Serif

Colors

Designer to choose colors to be used in the design.

Requirements
Must have
• See description
Nice to have
• See description
Should not have
• See description

```html
<!DOCTYPE html>
<html lang="en">
<head>
<meta charset="utf-8">
<title>Thank You For Ordering – Lumavela</title>
<link rel="stylesheet" href="https://fonts.googleapis.com/css2?family=Bodoni+Moda:opsz,wght@6..96,400;6..96,600;6..96,700&display=swap">
<style>
  :root {
    --ink: #444444;
    --ink-soft: #555555;
    --accent: #c8283a;
    --paper: #ffffff;
    --panel: #f6f6f6;
    --brand-grey: #cfcfcf;
    --media-warm: #b06a48;
    --media-light: #e9e4df;
  }
  * { margin: 0; padding: 0; box-sizing: border-box; }
  html, body { width: 1200px; height: 650px; overflow: hidden; background: var(--paper); }
  body { font-family: "Bodoni Moda", "Times New Roman", serif; color: var(--ink); }

  .canvas { position: relative; width: 1200px; height: 650px; overflow: hidden; background: var(--paper); }

  .side-panel {
    position: absolute; left: 760px; top: 60px; width: 440px; height: 525px;
    background: linear-gradient(120deg, rgba(246,246,246,0) 0%, var(--panel) 40%, rgba(246,246,246,0.6) 100%);
  }

  .close-button {
    position: absolute; left: 1050px; top: 29px; width: 32px; height: 32px;
  }

  .headline {
    position: absolute; left: 150px; top: 104px;
    font-size: 38px; font-weight: 700; letter-spacing: -1.6px; line-height: 1;
    color: var(--ink); white-space: nowrap;
  }

  .confirmation {
    position: absolute; left: 148px; top: 176px; width: 400px;
    font-size: 16.5px; line-height: 22px; letter-spacing: -0.4px; color: var(--ink-soft);
  }
  .confirmation strong { font-weight: 600; color: var(--ink); }
  .confirmation .contact-email { color: var(--accent); font-weight: 600; }

  .articles-intro {
    position: absolute; left: 150px; top: 295px; width: 400px;
    font-size: 16.5px; line-height: 22px; font-weight: 600; letter-spacing: -0.5px; color: var(--ink);
  }

  .article-list {
    position: absolute; left: 164px; top: 355px; list-style: none;
    font-size: 16.5px; line-height: 22.5px; letter-spacing: -0.4px; color: var(--ink-soft);
  }
  .article-list li { position: relative; padding-left: 22px; }
  .article-list li::before {
    content: ""; position: absolute; left: 2px; top: 9px;
    width: 5px; height: 5px; border-radius: 50%; background: var(--accent);
  }

  .brand-name {
    position: absolute; left: 174px; top: 510px;
    font-size: 28px; font-weight: 700; letter-spacing: 1.5px; color: var(--brand-grey);
  }

  .video-card {
    position: absolute; left: 618px; top: 186px; width: 431px; height: 253px;
    border-radius: 7px; overflow: hidden;
    box-shadow: 0 18px 40px rgba(0,0,0,0.18);
  }
  .video-card .media-fill {
    position: absolute; inset: 0;
    background: linear-gradient(100deg, var(--media-warm) 0%, #c99478 30%, var(--media-light) 55%, #d9b9a4 80%, #a4583a 100%);
  }
  .video-card .video-controls { position: absolute; inset: 0; }

  .social-block {
    position: absolute; left: 622px; top: 470px; width: 430px;
    display: flex; align-items: center; justify-content: space-between;
  }
  .social-title {
    font-size: 16.5px; font-weight: 700; letter-spacing: -0.6px; color: var(--ink); white-space: nowrap;
  }
  .social-links { display: flex; gap: 14px; }
  .social-links a {
    font-size: 15px; font-weight: 700; color: var(--accent); text-decoration: none;
  }
</style>
</head>
<body>
<main class="canvas">
  <div class="side-panel"></div>

  <svg class="close-button" viewBox="0 0 32 32" aria-label="Close">
    <circle cx="16" cy="16" r="16" fill="var(--accent)"/>
    <path d="M10.5 10.5 L21.5 21.5 M21.5 10.5 L10.5 21.5" stroke="#fff" stroke-width="2" stroke-linecap="round"/>
  </svg>

  <h1 class="headline">THANK YOU FOR ORDERING!</h1>

  <p class="confirmation">
    <strong>You will receive a confirmation email shortly.</strong><br>
    For any questions or issues with your order, Please don’t hesitate to contact us at
    <span class="contact-email">info@lumavela.ro</span>
  </p>

  <p class="articles-intro">Here are some of our most popular articles<br>to keep you entertained untill the package arrives:</p>

  <ul class="article-list">
    <li>Best eye - creams for each pocket</li>
    <li>Must - have makeup products for summer</li>
    <li>Summer outfits for work</li>
    <li>The ultimate guide to the Purelayer skincare</li>
  </ul>

  <div class="brand-name">LUMAVELA</div>

  <figure class="video-card">
    <div class="media-fill" role="img" aria-label="Video still: a woman applying powder with a brush while looking into a compact mirror"></div>
    <svg class="video-controls" viewBox="0 0 431 253" aria-label="Play video">
      <circle cx="214" cy="130" r="24" fill="rgba(0,0,0,0.15)" stroke="#fff" stroke-width="2"/>
      <path d="M206 118 L226 130 L206 142 Z" fill="#fff"/>
      <line x1="25" y1="235" x2="409" y2="235" stroke="#fff" stroke-width="1.5" opacity="0.9"/>
      <circle cx="25" cy="235" r="5" fill="#fff"/>
    </svg>
  </figure>

  <div class="social-block">
    <span class="social-title">JOIN THE SQUAD ON SOCIAL MEDIA</span>
    <nav class="social-links">
      <a href="#">Flit</a>
      <a href="#">Pixo</a>
      <a href="#">Kin</a>
    </nav>
  </div>
</main>
</body>
</html>
```